We need a complete design for our construction company KELTO CONSTRUCTION based in Auckland New Zealand, we need a logo, website, business card, vehicle design etc..
We are a mid to high-end construction company who work mostly on residential projects and some commercial.

What we want to see in the design;
Professional,
Architectural,
Simple,
Alternative,

We want the design to communicate professionalism, high quality wormanship and and quality service.

Target Market(s)

People looking for a quality building/ construction company

Industry/Entity Type

Construction Company

Contact Information for Business Card

KELTO CONSTRUCTION.co.nz
Lino Verasek
lino@keltoconstruction.example.nz
021 5807 462

Logo Text

KELTO CONSTRUCTION

Number of Pages Required

5+ page

Font styles to use
Sans Serif

Colors

Designer to choose colors to be used in the design.

Requirements
Must have
• Must appear high end, professional, quality, be simple, easy to use, give security to potential clients
Nice to have
• high-quality photos of our recent projects
• about us page
• blog page
• contact us page
• high quality content
Should not have
• should not be hard to use and have too much going on.

```html
<!DOCTYPE html>
<html lang="en">
<head>
<meta charset="utf-8">
<title>Kelto Construction</title>
<link href="https://fonts.googleapis.com/css2?family=Lato:wght@300;400;700;900&family=Montserrat:wght@600;700&family=Open+Sans:ital,wght@1,400&display=swap" rel="stylesheet">
<style>
:root{
  --gold:#b5872a;
  --gold-dark:#9c7220;
  --navy:#1d3a7a;
  --ink:#222;
  --text:#666;
  --light:#f5f5f5;
  --white:#fff;
}
*{box-sizing:border-box;margin:0;padding:0}
html,body{width:1200px;height:3098px;overflow:hidden}
body{font-family:"Lato",sans-serif;color:var(--ink);background:var(--white);position:relative}
/* hero */
.hero{position:absolute;left:0;top:0;width:1200px;height:680px;
  background:linear-gradient(180deg,#16398c 0%,#3a5f9a 30%,#5a6f72 55%,#3f5b34 80%,#2d4426 100%)}
.hero-curve{position:absolute;left:0;top:620px;width:1200px;height:62px}
.brand{position:absolute;left:99px;top:8px}
.brand-dot{width:170px;height:170px;border-radius:50%;background:var(--gold)}
.brand-name{position:absolute;left:0;top:58px;width:170px;text-align:center;color:var(--white);font-weight:900;font-size:20px;line-height:1.2}
.nav{position:absolute;top:68px;right:80px;display:flex;gap:68px;align-items:center}
.nav a{color:var(--white);text-decoration:none;font-weight:700;font-size:15px;letter-spacing:.3px}
.nav a.active{color:var(--gold);border-bottom:2px solid var(--gold);padding-bottom:6px}
.hero-title{position:absolute;top:242px;width:1200px;text-align:center;color:var(--white);
  font-family:"Montserrat",sans-serif;font-weight:700;font-size:82px;letter-spacing:1px}
.hero-sub{position:absolute;top:332px;width:1200px;text-align:center;color:var(--white);font-size:18px;font-weight:700}
.btn-solid{position:absolute;left:506px;top:386px;width:188px;height:48px;background:var(--gold);color:var(--white);
  font-size:21px;display:flex;align-items:center;justify-content:center}
.dots{position:absolute;top:576px;left:556px;display:flex;gap:10px}
.dots span{width:14px;height:14px;border-radius:50%;background:var(--white)}
.dots span.active{background:transparent;border:2px solid var(--white)}
/* welcome */
.h-gold{position:absolute;width:1200px;text-align:center;color:var(--gold);font-family:"Montserrat",sans-serif;font-weight:700;font-size:40px}
.para{position:absolute;left:130px;width:940px;text-align:center;font-size:14px;line-height:27px;color:var(--text)}
.btn-line{position:absolute;width:258px;height:50px;border:2px solid var(--gold);color:var(--gold);font-size:16px;
  display:flex;align-items:center;justify-content:center;letter-spacing:.5px}
/* about */
.about{position:absolute;left:0;top:1130px;width:1200px;height:430px;
  background:linear-gradient(135deg,#4a6785 0%,#3b5870 40%,#2f4a4a 75%,#27423a 100%)}
.about-title{position:absolute;top:58px;width:1200px;text-align:center;color:var(--white);font-weight:300;font-size:50px}
.about .para{color:var(--white);left:185px;width:830px;font-size:13.5px;line-height:25px}
.about .btn-line{border-color:var(--white);color:var(--white)}
/* projects */
.h-plain{position:absolute;width:1200px;text-align:center;font-weight:300;font-size:38px;color:var(--ink)}
.tile{position:absolute;display:flex;align-items:center;justify-content:center;text-align:center;color:var(--white);
  font-family:"Montserrat",sans-serif;font-weight:700;font-size:24px;line-height:1.2;white-space:nowrap}
.testi{position:absolute;left:0;top:2131px;width:1200px;height:622px;background:var(--light)}
.quote{position:absolute;left:170px;width:860px;top:2330px;text-align:center;font-family:"Open Sans",sans-serif;font-style:italic;
  font-size:19px;line-height:28px;color:#555}
.qmark{position:absolute;font-family:Georgia,serif;font-size:80px;color:#d4d4d4;line-height:1}
.arrow{position:absolute;top:2390px}
.avatar{position:absolute;left:532px;top:2497px;width:136px;height:136px;border-radius:50%;border:5px solid var(--white);
  background:linear-gradient(180deg,#7a8a9a,#4d5a48);box-shadow:0 0 0 2px #ddd}
.client{position:absolute;top:2650px;width:1200px;text-align:center;font-size:17px;letter-spacing:2px;color:#444}
/* footer */
.footer{position:absolute;left:0;top:2753px;width:1200px;height:345px;background:var(--gold);color:var(--white)}
.f-head{position:absolute;top:46px;font-size:18px;font-weight:700;letter-spacing:.5px}
.f-list{position:absolute;top:90px;list-style:none;font-size:14px;line-height:32px}
.f-text{position:absolute;font-size:14px;line-height:28px}
.f-div{position:absolute;left:410px;top:46px;width:1px;height:180px;background:rgba(255,255,255,.25)}
.sub-form{position:absolute;left:774px;top:112px;display:flex}
.sub-input{width:222px;height:40px;background:var(--white);color:#aaa;font-size:13px;padding:12px 14px;letter-spacing:.5px}
.sub-btn{width:106px;height:40px;background:var(--gold-dark);font-size:14px;display:flex;align-items:center;justify-content:center}
.socials{position:absolute;left:774px;top:170px;display:flex;gap:10px}
.socials span{width:38px;height:38px;border-radius:50%;background:var(--white)}
.f-rule{position:absolute;left:99px;top:272px;width:1002px;height:1px;background:rgba(255,255,255,.35)}
.copy{position:absolute;left:99px;top:295px;font-size:14px}
</style>
</head>
<body>

<section class="hero" role="img" aria-label="City skyline and harbour seen from a green park hillside"></section>
<svg class="hero-curve" viewBox="0 0 1200 62" preserveAspectRatio="none"><path d="M0 62 Q600 -30 1200 62 Z" fill="#fff"/></svg>

<div class="brand"><div class="brand-dot"></div><div class="brand-name">KELTO<br>CONSTRUCTION</div></div>
<nav class="nav">
  <a class="active">HOME</a><a>ABOUT US</a><a>PROJECTS</a><a>BLOG</a><a>CONTACT US</a>
  <svg width="16" height="16" viewBox="0 0 16 16"><circle cx="6.5" cy="6.5" r="4.5" fill="none" stroke="#fff" stroke-width="2"/><path d="M10 10l4 4" stroke="#fff" stroke-width="2.4"/></svg>
</nav>
<h1 class="hero-title">KELTO CONSTRUCTION</h1>
<p class="hero-sub">We are a mid to high-end construction company who work mostly on residential projects and some commercial.</p>
<div class="btn-solid">GET IN TOUCH</div>
<div class="dots"><span class="active"></span><span></span><span></span><span></span></div>

<h2 class="h-gold" style="top:724px">WELCOME TO KELTO CONSTRUCTION</h2>
<p class="para" style="top:792px">Sed ut perspiciatis unde omnis iste natus error sit voluptatem accusantium doloremque laudantium, totam rem aperiam, eaque ipsa quae ab illo inventore veritatis et quasi architecto beatae vitae dicta sunt explicabo. Nemo enim ipsam voluptatem quia voluptas sit aspernatur aut odit aut fugit, sed quia consequuntur magni dolores eos qui ratione voluptatem sequi nesciunt.</p>
<p class="para" style="top:888px">Neque porro quisquam est, qui dolorem ipsum quia dolor sit amet, consectetur, adipisci velit, sed quia non numquam eius modi tempora incidunt ut labore et dolore magnam aliquam quaerat voluptatem</p>
<div class="btn-line" style="left:471px;top:979px">READ MORE INFORMATION</div>

<section class="about" role="img" aria-label="Aerial view of a coastal suburb with houses and sea">
  <h2 class="about-title">ABOUT KELTO CONSTRUCTION</h2>
  <p class="para" style="top:134px">At vero eos et accusamus et iusto odio dignissimos ducimus qui blanditiis praesentium voluptatum deleniti atque corrupti quos dolores et quas molestias excepturi sint occaecati cupiditate non provident, similique sunt in culpa qui officia deserunt mollitia animi, id est laborum et dolorum fuga. Et harum quidem rerum facilis est et expedita distinctio.</p>
  <p class="para" style="top:220px">Quis autem vel eum iure reprehenderit qui in ea voluptate velit esse quam nihil molestiae consequatur, vel illum qui dolorem eum fugiat quo voluptas nulla pariatur</p>
  <div class="btn-line" style="left:459px;top:301px;width:282px">READ MORE INFORMATION</div>
</section>

<h2 class="h-plain" style="top:1624px">OUR RECENT PROJECTS</h2>
<p class="para" style="top:1688px">At vero eos et accusamus et iusto odio dignissimos ducimus qui blanditiis praesentium voluptatum deleniti atque corrupti quos dolores et quas molestias excepturi sint occaecati cupiditate non provident, similique sunt in culpa qui officia deserunt mollitia animi.</p>

<div class="tile" style="left:99px;top:1793px;width:334px;height:202px;background:linear-gradient(160deg,#8a6a52,#4a3528)" role="img" aria-label="Timber house frame under construction">CONSUMERS BUILDING<br>HOUSES</div>
<div class="tile" style="left:433px;top:1793px;width:334px;height:202px;background:linear-gradient(160deg,#b8b0a0,#6f8a5a)" role="img" aria-label="Renovated apartment buildings with lawn">RENOVATING OR<br>UPGRADING</div>
<div class="tile" style="left:767px;top:1793px;width:334px;height:202px;background:linear-gradient(160deg,#c8ccd2,#5e6670)" role="img" aria-label="Modern residential houses">RESIDENTIAL<br>PROJECTS</div>
<div class="testi"></div>
<div class="tile" style="left:99px;top:1995px;width:1002px;height:180px;background:linear-gradient(180deg,#1e2a4a,#3a3040 70%,#6a4a30)" role="img" aria-label="Commercial apartment blocks at dusk">COMMERCIAL PROJECTS</div>

<h2 class="h-plain" style="top:2254px">CLIENT TESTIMONIALS</h2>
<span class="qmark" style="left:140px;top:2316px">&ldquo;</span>
<p class="quote">But I must explain to you how all this mistaken idea of denouncing pleasure and praising pain was born and I will give you a complete account of the system, and expound the actual teachings of the great explorer of the truth, the master-builder of human happiness. No one rejects, dislikes, or avoids pleasure itself, because it is pleasure, but because those who do not know how to pursue pleasure rationally encounter consequences that are extremely painful</p>
<span class="qmark" style="left:1005px;top:2440px">&rdquo;</span>
<svg class="arrow" style="left:100px" width="20" height="36" viewBox="0 0 20 36"><path d="M18 2L3 18l15 16" fill="none" stroke="#ccc" stroke-width="2"/></svg>
<svg class="arrow" style="left:1080px" width="20" height="36" viewBox="0 0 20 36"><path d="M2 2l15 16L2 34" fill="none" stroke="#ccc" stroke-width="2"/></svg>
<div class="avatar" role="img" aria-label="Client portrait in front of their new home"></div>
<p class="client">- ASSUMENDA EST</p>

<footer class="footer">
  <h3 class="f-head" style="left:99px">QUICK LINKS</h3>
  <ul class="f-list" style="left:99px"><li>Home</li><li>About Us</li><li>Projects</li><li>Blog</li><li>Contact Us</li></ul>
  <ul class="f-list" style="left:262px"><li>Terms of Service</li><li>Privacy Policy</li><li>Contact Us</li></ul>
  <div class="f-div"></div>
  <h3 class="f-head" style="left:487px">CONTACT INFO</h3>
  <p class="f-text" style="left:487px;top:88px;width:240px">KELTO CONSTRUCTION, Street Name, City Name, Country Code.</p>
  <p class="f-text" style="left:487px;top:148px">
    <svg width="14" height="14" viewBox="0 0 14 14" style="vertical-align:-2px;margin-right:10px"><rect width="14" height="14" rx="2" fill="#fff"/><path d="M4 3l2 2-1 1.5c.7 1.3 1.3 1.9 2.5 2.5L9 8l2 2-1.5 1.5C6 11 3 8 2.5 4.5z" fill="#b5872a"/></svg>+00 123 45 67 890</p>
  <p class="f-text" style="left:487px;top:180px">
    <svg width="14" height="12" viewBox="0 0 14 12" style="vertical-align:-1px;margin-right:10px"><rect width="14" height="12" fill="#fff"/><path d="M0 0l7 6 7-6" fill="none" stroke="#b5872a" stroke-width="1.5"/></svg>info@keltoconstruction.example.nz</p>
  <h3 class="f-head" style="left:774px">SIGN UP FOR NEWSLETTERS</h3>
  <p class="f-text" style="left:774px;top:80px">Please sign up here for latest news</p>
  <div class="sub-form"><div class="sub-input">EMAIL ADDRESS</div><div class="sub-btn">SUBSCRIBE</div></div>
  <div class="socials"><span></span><span></span><span></span><span></span></div>
  <div class="f-rule"></div>
  <p class="copy">© 2018 KELTO CONSTRUCTION. All right reserved . Term of Use</p>
</footer>

</body>
</html>
```